Business card for medical clinic

I need an upmarket, modern medical/health business card for my clinic

Contact Information for Business Card

name, address, email, qr code

```html
<!DOCTYPE html>
<html lang="en">
<head>
<meta charset="utf-8">
<title>Meridian Care Clinic – Business Card</title>
<link rel="stylesheet" href="https://fonts.googleapis.com/css2?family=Tinos:wght@400;700&display=swap">
<style>
  :root {
    --bg: #e4e5e9;
    --navy: #14244a;
    --navy-deep: #0f1a3c;
    --blue: #1f8fd6;
    --sky: #3aa9e6;
    --steel: #2d5a86;
    --ink: #1a2747;
    --text: #333844;
    --card: #ffffff;
  }
  * { box-sizing: border-box; margin: 0; padding: 0; }
  html, body { width: 1200px; height: 800px; overflow: hidden; }
  body {
    background: var(--bg);
    font-family: "Tinos", "Times New Roman", serif;
    display: flex;
    align-items: center;
    justify-content: center;
    gap: 50px;
  }
  .card {
    width: 540px;
    height: 310px;
    position: relative;
    overflow: hidden;
    box-shadow: 0 6px 18px rgba(0,0,0,0.18);
  }
  /* Back side */
  .card-back {
    background: var(--navy-deep);
  }
  .card-back .pattern {
    position: absolute; inset: 0;
    background: linear-gradient(160deg, #15244c 0%, #0f1a3c 60%, #0c1634 100%);
  }
  .card-back .brand {
    position: absolute;
    left: 50%; top: 50%;
    transform: translate(-50%, -50%);
    display: flex; align-items: center; gap: 10px;
    color: #ffffff;
    font-size: 20px;
    letter-spacing: 1.5px;
    text-transform: uppercase;
    white-space: nowrap;
  }
  .brand-dot {
    width: 26px; height: 26px;
    border-radius: 50%;
    border: 2px solid currentColor;
  }
  /* Front side */
  .card-front { background: var(--card); }
  .card-front .brand {
    position: absolute;
    right: 34px; top: 46px;
    display: flex; align-items: center; gap: 12px;
    color: var(--steel);
    font-size: 24px;
    letter-spacing: 2px;
    text-transform: uppercase;
    white-space: nowrap;
  }
  .card-front .brand .brand-dot { width: 40px; height: 40px; border-color: var(--blue); }
  .rule {
    position: absolute;
    left: 22px; right: 22px;
    height: 1px;
    background: var(--sky);
  }
  .rule-top { top: 118px; }
  .rule-bottom { top: 252px; }
  .contact-left {
    position: absolute;
    left: 24px; top: 132px;
    font-size: 14px;
    color: var(--text);
    line-height: 1.55;
  }
  .contact-right {
    position: absolute;
    right: 24px; top: 196px;
    font-size: 14px;
    color: var(--text);
    line-height: 1.6;
    text-align: right;
  }
  .line { display: flex; align-items: center; gap: 7px; }
  .contact-right .line { justify-content: flex-end; }
  .icon { width: 12px; height: 12px; flex: none; }
  .person {
    position: absolute;
    left: 250px; top: 138px;
    text-align: center;
    color: var(--ink);
  }
  .person-name {
    font-weight: 700;
    font-size: 17px;
    letter-spacing: 1px;
    text-transform: uppercase;
  }
  .person-role { font-size: 14px; color: var(--text); margin-top: 2px; }
  .bands {
    position: absolute; left: 0; right: 0; bottom: 0;
    height: 46px;
  }
  .bands svg { display: block; width: 100%; height: 100%; }
</style>
</head>
<body>

  <section class="card card-back" aria-label="Card back">
    <div class="pattern" role="img" aria-label="Repeating clinic name pattern in muted blue on navy"></div>
    <div class="brand"><span class="brand-dot"></span>Meridian Care Clinic</div>
  </section>

  <section class="card card-front" aria-label="Card front">
    <div class="brand"><span class="brand-dot"></span>Meridian Care Clinic</div>

    <div class="rule rule-top"></div>

    <div class="contact-left">
      <div class="line">
        <svg class="icon" viewBox="0 0 12 12"><path d="M2.5 1 L4.5 1 L5.2 3.6 L4 4.6 C4.6 6 6 7.4 7.4 8 L8.4 6.8 L11 7.5 L11 9.5 C11 10.3 10.3 11 9.5 11 C5 11 1 7 1 2.5 C1 1.7 1.7 1 2.5 1 Z" fill="var(--sky)"/></svg>
        300-400-7000
      </div>
      <div class="line">
        <svg class="icon" viewBox="0 0 12 12"><path d="M6 0.5 C3.8 0.5 2.2 2.1 2.2 4.2 C2.2 7 6 11.5 6 11.5 C6 11.5 9.8 7 9.8 4.2 C9.8 2.1 8.2 0.5 6 0.5 Z" fill="var(--sky)"/><circle cx="6" cy="4.2" r="1.4" fill="#fff"/></svg>
        00 dummy city, dummy place 0000
      </div>
    </div>

    <div class="person">
      <div class="person-name">Alex Morgan</div>
      <div class="person-role">Director</div>
    </div>

    <div class="contact-right">
      <div class="line">
        info@meridiancareclinic.com
        <svg class="icon" viewBox="0 0 12 12"><rect x="0.5" y="2" width="11" height="8" fill="var(--sky)"/><path d="M0.5 2 L6 6.5 L11.5 2" fill="none" stroke="#fff" stroke-width="1"/></svg>
      </div>
      <div class="line">
        www.meridiancareclinic.com
        <svg class="icon" viewBox="0 0 12 12" fill="none" stroke="var(--sky)" stroke-width="1"><circle cx="6" cy="6" r="5.3"/><ellipse cx="6" cy="6" rx="2.3" ry="5.3"/><path d="M0.7 6 H11.3 M1.6 3.3 H10.4 M1.6 8.7 H10.4"/></svg>
      </div>
    </div>

    <div class="rule rule-bottom"></div>

    <div class="bands">
      <svg viewBox="0 0 540 46" preserveAspectRatio="none">
        <rect x="0" y="0" width="540" height="14" fill="var(--navy)"/>
        <rect x="0" y="14" width="540" height="16" fill="var(--steel)"/>
        <rect x="0" y="30" width="540" height="16" fill="var(--sky)"/>
      </svg>
    </div>
  </section>

</body>
</html>
```